Heritage Hollow Business Cards

Require a business card design. <br/><br/>Needs to include logo (either round or long version) plus these details:<br/>Maya Torvell<br/>Heritage Hollow<br/>maya@kelvadtrading.com.au<br/>02 6481 7395<br/>PO Box Glenwarra NSW 2791<br/>www.heritagehollow.com.au<br/><br/>I need in an editable format so that I can create for multiple staff members. <br/><br/>

Target Market(s)

We are an online store selling renovation products to home owners are builders. Looking for a classic classy design.

Industry/Entity Type

Home And Garden

Contact Information for Business Card

Maya Torvell
Heritage Hollow
maya@kelvadtrading.com.au
02 6481 7395
PO Box Glenwarra NSW 2791
www.heritagehollow.com.au

Colors

Designer to choose colors to be used in the design.

Requirements
Must have
• Must include Logo.

```html
<!DOCTYPE html>
<html lang="en">
<head>
<meta charset="utf-8">
<title>Heritage Hollow Business Cards</title>
<link href="https://fonts.googleapis.com/css2?family=Roboto:wght@300;400;500&family=Alegreya+SC:wght@400&display=swap" rel="stylesheet">
<style>
  :root {
    --backdrop: #dfe0e4;
    --card-dark-1: #1c1c1c;
    --card-dark-2: #050505;
    --mark-grey: #4a4a4a;
    --card-light: #ededed;
    --ink: #151515;
    --ink-soft: #2b2b2b;
  }
  * { margin: 0; padding: 0; box-sizing: border-box; }
  html, body { width: 1200px; height: 1200px; overflow: hidden; }
  body { background: var(--backdrop); position: relative; font-family: "Roboto", sans-serif; }

  .card {
    position: absolute;
    left: 269px;
    width: 663px;
    height: 379px;
    border-radius: 18px;
  }
  .card--front {
    top: 178px;
    background: radial-gradient(ellipse at 40% 20%, var(--card-dark-1), var(--card-dark-2) 75%);
  }
  .card--back {
    top: 643px;
    background: var(--card-light);
  }

  .brand-mark {
    position: absolute;
    left: 0; right: 0;
    top: 190px;
    text-align: center;
    font-family: "Roboto", sans-serif;
    font-weight: 400;
    font-size: 46px;
    color: var(--mark-grey);
    letter-spacing: 0.5px;
    padding-left: 60px;
  }

  .holder-name {
    position: absolute;
    right: 368px;
    top: 180px;
    font-family: "Alegreya SC", serif;
    font-size: 30px;
    color: var(--ink-soft);
    white-space: nowrap;
  }
  .divider {
    position: absolute;
    left: 309px;
    top: 143px;
    width: 1.5px;
    height: 94px;
    background: var(--ink);
  }
  .contact {
    position: absolute;
    left: 325px;
    top: 141px;
  }
  .contact__company {
    font-size: 17.5px;
    font-weight: 500;
    color: var(--ink);
    margin-bottom: 4px;
  }
  .contact__list { list-style: none; }
  .contact__item {
    display: flex;
    align-items: center;
    gap: 5px;
    font-size: 13px;
    font-weight: 300;
    color: var(--ink);
    height: 19.5px;
  }
  .contact__item svg { width: 10px; height: 10px; flex: none; }
  .contact__item strong { font-weight: 500; }
</style>
</head>
<body>
  <section class="card card--front">
    <div class="brand-mark">Heritage Hollow</div>
  </section>

  <section class="card card--back">
    <div class="holder-name">MAYA TORVELL</div>
    <div class="divider"></div>
    <div class="contact">
      <div class="contact__company">HERITAGE HOLLOW</div>
      <ul class="contact__list">
        <li class="contact__item">
          <svg viewBox="0 0 10 10" aria-hidden="true"><path d="M5 0.3a3.2 3.2 0 0 0-3.2 3.2C1.8 6 5 9.7 5 9.7S8.2 6 8.2 3.5A3.2 3.2 0 0 0 5 .3zm0 4.4a1.2 1.2 0 1 1 0-2.4 1.2 1.2 0 0 1 0 2.4z" fill="#151515"/></svg>
          PO Box Glenwarra NSW 2791
        </li>
        <li class="contact__item">
          <svg viewBox="0 0 10 10" aria-hidden="true"><path d="M2.2.6 3.7 2.3 2.9 3.5c.6 1.4 1.9 2.6 3.3 3.3l1.2-.8L9.2 7.6 8.1 9.2C4.4 9 .9 5.5.8 1.8z" fill="none" stroke="#151515" stroke-width="1"/></svg>
          02 6481 7395
        </li>
        <li class="contact__item">
          <svg viewBox="0 0 10 10" aria-hidden="true"><rect x="0.7" y="2" width="8.6" height="6.4" fill="none" stroke="#151515" stroke-width="1"/><path d="M.7 2 5 5.6 9.3 2" fill="none" stroke="#151515" stroke-width="1"/></svg>
          maya@kelvadtrading.com.au
        </li>
        <li class="contact__item">
          <svg viewBox="0 0 10 10" aria-hidden="true"><g fill="none" stroke="#151515" stroke-width=".8"><circle cx="5" cy="5" r="4.4"/><ellipse cx="5" cy="5" rx="1.9" ry="4.4"/><path d="M.6 5h8.8M1.3 2.8h7.4M1.3 7.2h7.4"/></g></svg>
          <span>www.<strong>heritagehollow</strong>.com.au</span>
        </li>
      </ul>
    </div>
  </section>
</body>
</html>
```